Business Card Design

New business card design

Target Market(s)

Residential & Commercial Property Managers

Industry/Entity Type

Plumbing Services

Contact Information for Business Card

Name - Rowan Keddle, title - Director, Phone Number - 0431 286 517, email - rowan@tbk-plumbing.com.au, Company ABN - 73 215 904 386,

Font styles to use
Sans Serif

Colors
0054AA
0677BA
7BADD7
CADEEF
E8F1F8

```html
<!DOCTYPE html>
<html lang="en">
<head>
<meta charset="utf-8">
<title>TBK Plumbing Services – Business Card</title>
<link rel="stylesheet" href="https://fonts.googleapis.com/css2?family=Poppins:wght@300;400;500;600&display=swap">
<style>
  :root {
    --stage: #222222;
    --card: #ffffff;
    --edge: #29a8e0;
    --ink: #1d2630;
    --accent: #29a8e0;
    --muted: #7a6e66;
    --tint: #e8f1f8;
  }
  * { margin: 0; padding: 0; box-sizing: border-box; }
  html, body {
    width: 1200px; height: 711px; overflow: hidden;
    background: var(--stage);
    font-family: "Poppins", sans-serif;
  }
  .stage {
    width: 1200px; height: 711px;
    display: flex; align-items: center; justify-content: center; gap: 40px;
  }
  .card {
    position: relative;
    width: 540px; height: 310px;
    background: var(--card);
    border-radius: 22px;
    border-bottom: 5px solid var(--edge);
    border-left: 3px solid var(--edge);
    overflow: hidden;
  }
  .brand { display: flex; align-items: center; gap: 12px; }
  .brand-name {
    font-weight: 400; color: var(--ink);
    letter-spacing: 4px; line-height: 1;
  }
  .brand-dot { border-radius: 50%; background: var(--accent); }
  .tagline {
    font-weight: 400; color: var(--muted);
    text-transform: lowercase;
  }
  /* Front */
  .card-front { display: flex; flex-direction: column; align-items: center; justify-content: center; }
  .card-front .brand-name { font-size: 104px; }
  .card-front .brand-dot { width: 22px; height: 22px; margin-top: 40px; }
  .card-front .tagline { font-size: 15px; letter-spacing: 14px; margin-top: 12px; margin-left: 14px; }
  /* Back */
  .card-back .brand { position: absolute; left: 34px; top: 32px; }
  .card-back .brand-name { font-size: 64px; }
  .card-back .brand-dot { width: 14px; height: 14px; margin-top: 24px; }
  .card-back .tagline { position: absolute; left: 38px; top: 108px; font-size: 10px; letter-spacing: 8px; }
  .tint-panel {
    position: absolute; right: 0; top: 0; width: 210px; height: 100%;
    background: linear-gradient(180deg, var(--tint), #f6f9fc);
  }
  .name-block { position: absolute; right: 40px; top: 84px; text-align: right; }
  .person { font-size: 26px; line-height: 1.1; }
  .person .first { color: var(--accent); font-weight: 600; }
  .person .last { color: var(--muted); font-weight: 300; }
  .role { font-size: 13px; color: var(--ink); font-weight: 400; margin-top: 2px; }
  .edge-tab {
    position: absolute; right: 0; top: 78px; width: 22px; height: 46px;
    background: var(--accent);
  }
  .abn { position: absolute; left: 38px; top: 184px; font-size: 13px; color: var(--accent); font-weight: 300; }
  .contacts { position: absolute; left: 38px; top: 214px; list-style: none; }
  .contacts li {
    display: flex; align-items: center; gap: 10px;
    font-size: 14px; color: var(--ink); line-height: 24px;
  }
  .contacts svg { width: 15px; height: 15px; flex: none; }
</style>
</head>
<body>
<main class="stage">
  <section class="card card-front" aria-label="Card front">
    <div class="brand">
      <span class="brand-name">tbk</span>
      <span class="brand-dot"></span>
    </div>
    <p class="tagline">plumbing services</p>
  </section>

  <section class="card card-back" aria-label="Card back">
    <div class="tint-panel"></div>
    <div class="brand">
      <span class="brand-name">tbk</span>
      <span class="brand-dot"></span>
    </div>
    <p class="tagline">plumbing services</p>
    <span class="edge-tab"></span>
    <div class="name-block">
      <p class="person"><span class="first">Rowan</span> <span class="last">Keddle</span></p>
      <p class="role">Director</p>
    </div>
    <p class="abn">ABN - 73 215 904 386</p>
    <ul class="contacts">
      <li>
        <svg viewBox="0 0 16 16" aria-hidden="true"><path fill="#29a8e0" d="M3.5 1.5l2.3 0 1 3.2-1.6 1.2c.8 1.8 2.1 3.1 3.9 3.9l1.2-1.6 3.2 1v2.3c0 .9-.7 1.5-1.6 1.5C6.5 13 3 9.5 2 3.1 2 2.2 2.6 1.5 3.5 1.5z"/></svg>
        <span>0431 286 517</span>
      </li>
      <li>
        <svg viewBox="0 0 16 16" aria-hidden="true"><circle cx="8" cy="8" r="6.5" fill="none" stroke="#29a8e0" stroke-width="1.4"/><path d="M1.5 8h13M8 1.5c2.2 2 2.2 11 0 13M8 1.5c-2.2 2-2.2 11 0 13" fill="none" stroke="#29a8e0" stroke-width="1.2"/></svg>
        <span>www.tbk-plumbing.com.au</span>
      </li>
      <li>
        <svg viewBox="0 0 16 16" aria-hidden="true"><rect x="1.5" y="3.5" width="13" height="9" rx="1" fill="none" stroke="#29a8e0" stroke-width="1.4"/><path d="M1.8 4l6.2 5 6.2-5" fill="none" stroke="#29a8e0" stroke-width="1.4"/></svg>
        <span>rowan@tbk-plumbing.com.au</span>
      </li>
    </ul>
  </section>
</main>
</body>
</html>
```